Modern business card design for professional copywriter

I'd like a business card design that I can use to have my cards printed out by quillprint.com as a squared corners business card (see artwork and design guidelines here: https://help.quillprint.com/hc/en-gb/sections/200570950-QUILL-Product-Templates)

The design should be clean and modern and reflect the colours, tone and branding on my website: https://tessavorrin.com.au

Target Market(s)

Professionals, B2B small business owners

Industry/Entity Type

Business

Contact Information for Business Card

Tessa Vorrin
m: 0468 905 327
e: tessa@tessavorrin.com.au
w: tessavorrin.com.au

Font styles to use
Sans Serif

Requirements
Must have
• Tagline: "Smart copywriting for clever business people"
• Brand colours: fd8000, 009984, 666666 and black
Nice to have

```html
<!DOCTYPE html>
<html lang="en">
<head>
<meta charset="utf-8">
<title>Tessa Vorrin – Business Card</title>
<link href="https://fonts.googleapis.com/css2?family=Jost:wght@400;500&display=swap" rel="stylesheet">
<style>
  :root {
    --teal: #169b86;
    --teal-text: #009984;
    --orange: #fd8000;
    --grey: #666666;
    --ink: #2a2a2a;
    --paper: #ffffff;
    --backdrop: #eeece6;
  }
  * { box-sizing: border-box; margin: 0; padding: 0; }
  html, body {
    width: 1200px; height: 929px; overflow: hidden;
    background: var(--backdrop);
    font-family: "Jost", "Futura", sans-serif;
  }
  .stage { position: relative; width: 1200px; height: 929px; }
  .card {
    position: absolute;
    width: 520px; height: 336px;
    box-shadow: 0 6px 14px rgba(0,0,0,0.18);
  }
  .card--front { left: 60px; top: 120px; background: var(--teal); }
  .card--back { left: 620px; top: 473px; background: var(--paper); }

  .brand-name {
    position: absolute;
    font-weight: 400;
    letter-spacing: -0.5px;
    white-space: nowrap;
    display: flex; align-items: center; gap: 10px;
  }
  .brand-name .dot { width: 14px; height: 14px; border-radius: 50%; }
  .card--front .brand-name {
    left: 0; right: 0; top: 118px; justify-content: center;
    font-size: 44px; color: #fff;
  }
  .card--front .brand-name .dot { background: #fff; }
  .card--back .brand-name {
    right: 34px; top: 34px; font-size: 34px; color: var(--orange);
  }
  .card--back .brand-name .dot { background: var(--orange); width: 11px; height: 11px; }

  .tagline {
    position: absolute; left: 0; right: 0; bottom: 36px;
    text-align: center; color: #fff;
    font-size: 13px; font-weight: 500; letter-spacing: 1px;
  }

  .contact { position: absolute; left: 40px; bottom: 34px; }
  .contact__name { color: var(--teal-text); font-size: 20px; font-weight: 500; line-height: 1.1; }
  .contact__role { color: var(--ink); font-size: 18px; font-weight: 500; margin-bottom: 12px; }
  .contact__list { list-style: none; }
  .contact__item {
    display: flex; align-items: center; gap: 10px;
    color: var(--grey); font-size: 15px; line-height: 22px;
  }
  .contact__item svg { width: 13px; height: 13px; flex: none; }
</style>
</head>
<body>
<main class="stage">
  <section class="card card--front" aria-label="Card front">
    <div class="brand-name"><span class="dot"></span>Tessa Vorrin</div>
    <p class="tagline">Smart copywriting for clever business people</p>
  </section>

  <section class="card card--back" aria-label="Card back">
    <div class="brand-name"><span class="dot"></span>Tessa Vorrin</div>
    <div class="contact">
      <p class="contact__name">Tessa Vorrin</p>
      <p class="contact__role">Copywriter</p>
      <ul class="contact__list">
        <li class="contact__item">
          <svg viewBox="0 0 13 13" aria-hidden="true"><rect x="3" y="1" width="7" height="11" rx="1" fill="none" stroke="#fd8000" stroke-width="1.6"/></svg>
          0468 905 327
        </li>
        <li class="contact__item">
          <svg viewBox="0 0 13 13" aria-hidden="true"><rect x="1" y="3" width="11" height="8" fill="#fd8000"/><path d="M1 3 L6.5 7.5 L12 3" fill="none" stroke="#fff" stroke-width="1"/></svg>
          tessa@tessavorrin.com.au
        </li>
        <li class="contact__item">
          <svg viewBox="0 0 13 13" aria-hidden="true"><circle cx="5.5" cy="5.5" r="3.8" fill="none" stroke="#fd8000" stroke-width="1.8"/><line x1="8.3" y1="8.3" x2="12" y2="12" stroke="#fd8000" stroke-width="2"/></svg>
          tessavorrin.com.au
        </li>
      </ul>
    </div>
  </section>
</main>
</body>
</html>
```